Wordpress Theme for Medical Clinics

** Please view updated Sitemap2.pdf doc to clarify some confusion ***

This is a multiuser WordPress subscription site for medical clinics. Please see attachment for sitemap. Please do not include extra content like social media icons, search bars, or images. If you have questions, please ask for clarification.
The site contains the following pages and sub-pages:

1. Home
2. Our Clinic
2a. Our Clinic > Mission
2b. Our Clinic > Services
2c. Our Clinic > Clinic Policies
2d. Our Clinic > Schedules
3. Our Staff
3a. Our Staff > [Staff member page]
4. Resources
4a. Resources > Patient Health (index)
4b. Resources > Patient Health (index) > [post]
4c. Resources > Links
4d. Resources > Forms
5. Alerts
5a. Alerts > [Alert Page]
6. Contact Us

Includes the Following Pages, Subpages, and Content
1. Home
a. About Us
b. Our Staff
c. Bulletins
d. Accepting New Patients (shown as an alert widget)
e. Links
i. Physician Toolbox
ii. Book an Appointment
f. Clinic Policies
i. Show first 3 policies (e.g. Late Arrivals, Missed Appointments, Fees)
ii. Link to Clinic Policies page
g. Primary widget (displayed on all pages)
i. Hours of operation
ii. Contact Info
1. Tel
2. Fax
3. Email
4. Address
5. Get directions (link to Google Maps)
2. Our Clinic
a. Main Page
i. Clinic Name
ii. Overview
iii. Languages Spoken
iv. Secondary Navigation
1. Mission
2. Services
3. Clinic Policies
4. Schedules (see attachment)
b. Our Clinic > Mission
c. Our Clinic > Services
i. For each service include service TITLE and DESCRIPTION
d. Our Clinic > Clinic Policies
i. For each policy include policy TITLE and DESCRIPTION
ii. Include the following policies in mockup
1. Late arrivals
2. Missed appointments
3. Fees for missed appointments
4. Referrals and follow-ups
5. Services not covered by RDA
6. Information for LTF patients
7. Medical Legal Reports
e. Our Clinic > Schedules
3. Our Staff
a. Main Page
i. Display a list of staff members. Include NAME and DESIGNATION
b. Our Staff > [Staff Name]
i. Include NAME, PICTURE, DESIGNATION, and BIO
4. Resources
a. Resources > Patient Health
i. Main Page
1. Posts (ordered by date)
a. Title
b. Summary
2. Side Navigation
a. Post Categories
ii. Patient Health > [post title]
1. Title
2. Post Category
3. Date
4. Author
5. Summary
6. Body
b. Resources > Links
1. Secondary Navigation - Categories
a. Sample Categories:
i. Local Services
ii. RDA and Drug Coverage
iii. Mental Health Resources
2. Category page
a. Include the following links in the 'Local Services' category
i. Hypertension clinics
ii. Home Care services
iii. Vaccine Clinics
c. Resources > Forms
i. Display a table with form TITLE and CATEGORY
ii. Side Navigation
1. Form Categories
a. Use the following sample Categories
i. Referrals
ii. Insurance
iii. Intake
iv. Discharge
v. Waivers
5. Alerts
a. Main page
i. List of all Alert posts
1. Include post TITLE as a link to the post
ii. Side Navigation
1. Alerts Archive
a. shown as Month + Number of posts
iii. Alerts > [Alert page]
1. Include TITLE, DATE, AUTHOR, BODY
6. Contact Us
a. Map
b. Hours of operation
c. Address
d. Phone number
e. Fax number
e. Fax number
f. Map
g. Email

Design notes:
- fixed width
- responsive (need designs for mobile, tablet, and desktop)
- simple, dark font, white background
- use Font Awesome icons where needed
- user adds own logo

Target Market(s)

Medical Clinics

Industry/Entity Type

Medical

Number of Pages Required

5+ page

Font styles to use
Serif
Sans Serif

Requirements
Must have
• Please keep designs very simple.
• Examples:
• https://www.quolbin.com/install
• http://www.ventrohax.com/company/about-us
• http://brindlequota.org/
• http://www.trosk.com/
Should not have
• Minimal or no use of shadows and gradients

```html
<!DOCTYPE html>
<html lang="en">
<head>
<meta charset="utf-8">
<title>Marlow Clinics</title>
<link href="https://fonts.googleapis.com/css2?family=Raleway:wght@400;500;600&family=Open+Sans:wght@400;600&display=swap" rel="stylesheet">
<style>
:root{
  --cyan:#1cb3d3;
  --cyan-box:#2fc3e3;
  --ink:#222;
  --muted:#666;
  --rule:#e3e3e3;
  --teal:#0e5160;
  --teal-dark:#0a4350;
  --btn-dark:#0c4a58;
  --footer-text:#cfe3e7;
  --hero-tone:#c9d4dc;
}
*{box-sizing:border-box;margin:0;padding:0}
html,body{width:921px;height:1200px;overflow:hidden;background:#fff}
body{position:relative;font-family:'Open Sans',sans-serif;color:var(--ink)}
a{text-decoration:none;color:inherit}
.abs{position:absolute}

.brand{left:144px;top:20px;font-family:'Raleway',sans-serif;font-size:25px;color:var(--cyan);font-weight:400}
.account{left:692px;top:6px;font-family:'Raleway',sans-serif;font-size:10px;color:#888}
.account span{margin:0 5px;color:#bbb}
.main-nav{top:36px;left:450px;font-family:'Raleway',sans-serif;font-size:11.5px;font-weight:500}
.main-nav a{position:absolute;white-space:nowrap;color:#222}
.main-nav a.current{color:var(--cyan)}

.dropdown{left:435px;top:58px;width:192px;height:117px;background:#f3f3f3;border:1px solid #ddd;z-index:3;padding:13px 0 0 19px}
.dropdown a{display:block;font-size:7.6px;color:#444;line-height:18.4px}

.hero{left:0;top:78px;width:921px;height:360px;background:var(--hero-tone)}
.hero-caption{left:146px;top:190px;width:326px;height:114px;background:var(--cyan-box);color:#fff;padding:18px 0 0 27px}
.hero-caption h1{font-family:'Raleway',sans-serif;font-weight:400;font-size:20.5px;line-height:24px}
.hero-caption h2{font-family:'Raleway',sans-serif;font-weight:400;font-size:14px;line-height:17px;margin-bottom:9px}
.hero-caption p{font-size:7.4px;line-height:13.5px}
.dots{top:413px;left:430px;display:flex;gap:4px}
.dots i{width:13px;height:13px;border-radius:50%;background:#2a7f91;display:block}
.dots i.on{background:var(--cyan)}

.feature{top:465px;width:200px}
.feature .photo{width:196px;height:129px;border:1px solid #ddd}
.feature h3{font-family:'Raleway',sans-serif;font-weight:500;font-size:14px;color:var(--cyan);margin-top:9px;line-height:18px}
.feature p{font-size:6.9px;line-height:12px;color:#444;margin-top:4px;white-space:nowrap}
.feature .more{display:block;font-family:'Raleway',sans-serif;font-weight:600;font-size:9.6px;color:var(--cyan);margin-top:10px}

.divider{left:146px;top:734px;width:629px;height:1px;background:var(--rule)}

.col{top:765px;width:215px}
.col h4{font-family:'Raleway',sans-serif;font-weight:400;font-size:16px;color:#222;line-height:20px;margin-bottom:11px}
.col h4.accent{color:var(--cyan)}
.col p{font-size:7.2px;line-height:12px;color:var(--muted);margin-bottom:8px;white-space:nowrap}
.checks{list-style:none;margin-top:3px}
.checks li{font-size:8px;color:#333;display:flex;align-items:center;gap:7px;height:20px}
.post{position:absolute;left:0}
.post .title{font-family:'Raleway',sans-serif;font-size:9.5px;color:#333;line-height:12px;margin-bottom:2px}
.post p{margin-bottom:2px}
.post .date{font-size:7.4px;color:var(--cyan);display:block}
.btn{height:26px;font-family:'Raleway',sans-serif;font-weight:600;font-size:10px;color:#fff;display:flex;align-items:center;justify-content:center;border-radius:2px}
.btn-light{left:149px;top:914px;width:105px;background:var(--cyan)}
.btn-dark{left:370px;top:914px;width:121px;background:var(--btn-dark)}

.footer{left:0;top:974px;width:921px;height:182px;background:var(--teal)}
.footer h5{position:absolute;top:32px;font-family:'Raleway',sans-serif;font-weight:600;font-size:11.5px;color:#fff}
.footer .links a{position:absolute;font-family:'Raleway',sans-serif;font-size:9.4px;color:#fff}
.tweet{position:absolute;left:370px;width:230px;font-size:7.3px;line-height:12px;color:var(--footer-text)}
.follow{position:absolute;left:628px;top:55px;font-size:7.4px;color:var(--footer-text)}
.bottom{left:0;top:1156px;width:921px;height:44px;background:var(--teal-dark);padding:17px 0 0 148px;font-size:7.3px;color:var(--footer-text)}
</style>
</head>
<body>

<header>
  <div class="abs brand">Marlow Clinics</div>
  <div class="abs account"><a href="#">Login</a><span>|</span><a href="#">Sign Up</a></div>
  <nav class="abs main-nav">
    <a class="current" style="left:0">Home</a>
    <a style="left:57px">Clinic</a>
    <a style="left:112px">Our Staff</a>
    <a style="left:183px">Resources</a>
    <a style="left:263px">Contact us</a>
  </nav>
  <div class="abs dropdown">
    <a href="#">About [Partial in widget]</a>
    <a href="#">Our Staff [Partial in widget]</a>
    <a href="#">Alerts/Bulletins [partial in widget]</a>
    <a href="#">Physician Toolbox [with External Link]</a>
    <a href="#">Book an Appointment [with External Link]</a>
  </div>
</header>

<section>
  <div class="abs hero" role="img" aria-label="Smiling doctor, nurse, mother and child in a bright clinic"></div>
  <div class="abs hero-caption">
    <h1>Curabitur aculis tempus eros</h1>
    <h2>Morbi diam mauris viverra in gravida</h2>
    <p>Aenean porttitor eros vel dolor Donec convallis pede venenatis nibh<br>Duis quam Nam eget lacus Aliquam erat volutpat</p>
  </div>
  <div class="abs dots"><i class="on"></i><i></i><i></i><i></i></div>
</section>

<section>
  <article class="abs feature" style="left:146px">
    <div class="photo" role="img" aria-label="Doctor and nurse attending a patient" style="background:#9fb3b1"></div>
    <h3>WHAT WE DO</h3>
    <p>Mauris vel lacus vitae felis vestibulum volutpat Etiam est<br>nunc venenatis in tristique eu imperdiet ac nisl Cum sociis<br>natoque penatibus et magnis dis parturient<br>montes nascetur ridiculus mus In iaculis facilisi</p>
    <a class="more" href="#">LEARN MORE &#8250;</a>
  </article>
  <article class="abs feature" style="left:362px">
    <div class="photo" role="img" aria-label="Doctor working at a laboratory microscope" style="background:#dbe3e8"></div>
    <h3>SERVICE PROVIDE</h3>
    <p>Mauris vel lacus vitae felis vestibulum volutpat Etiam est<br>nunc venenatis in tristique eu imperdiet ac nisl Cum sociis<br>natoque penatibus et magnis dis parturient<br>montes nascetur ridiculus mus In iaculis facilisi</p>
    <a class="more" href="#">LEARN MORE &#8250;</a>
  </article>
  <article class="abs feature" style="left:578px">
    <div class="photo" role="img" aria-label="Nurse with an elderly patient" style="background:#bccdda"></div>
    <h3>OUR DOCTORS</h3>
    <p>Mauris vel lacus vitae felis vestibulum volutpat Etiam est<br>nunc venenatis in tristique eu imperdiet ac nisl Cum sociis<br>natoque penatibus et magnis dis parturient<br>montes nascetur ridiculus mus In iaculis facilisi</p>
    <a class="more" href="#">LEARN MORE &#8250;</a>
  </article>
</section>

<div class="abs divider"></div>

<section>
  <div class="abs col" style="left:148px">
    <h4>Little About Us</h4>
    <p>Mauris vel lacus vitae felis vestibulum volutpat Etiam<br>est nunc venenatis in tristique eu imperdiet ac</p>
    <p>Duis non nunc Nulla rhoncus dictum metus Curabitur<br>tristique mi condimentum orci Phasellus<br>pellentesque aliquam enim Proin dui lectus cursus eu<br>mattis laoreet viverra sit amet quam Curabitur vel<br>dolor ultrices ipsum dictum tristique Praesent vitae<br>lacus Ut velit enim vestibulum non</p>
  </div>
  <div class="abs col" style="left:367px">
    <h4>Medical Services</h4>
    <p style="margin-top:-2px">Mauris vel lacus vitae felis vestibulum volutpat Etiam est<br>nunc venenatis in tristique eu imperdiet ac</p>
    <ul class="checks">
      <li><svg width="10" height="10" viewBox="0 0 10 10"><circle cx="5" cy="5" r="5" fill="#1cb3d3"/><path d="M2.6 5.1l1.6 1.6 3.2-3.3" stroke="#fff" stroke-width="1.3" fill="none"/></svg>Duis non nunc Nulla</li>
      <li><svg width="10" height="10" viewBox="0 0 10 10"><circle cx="5" cy="5" r="5" fill="#1cb3d3"/><path d="M2.6 5.1l1.6 1.6 3.2-3.3" stroke="#fff" stroke-width="1.3" fill="none"/></svg>Ahoncus dictum metus</li>
      <li><svg width="10" height="10" viewBox="0 0 10 10"><circle cx="5" cy="5" r="5" fill="#1cb3d3"/><path d="M2.6 5.1l1.6 1.6 3.2-3.3" stroke="#fff" stroke-width="1.3" fill="none"/></svg>Curabitur tristique</li>
      <li><svg width="10" height="10" viewBox="0 0 10 10"><circle cx="5" cy="5" r="5" fill="#1cb3d3"/><path d="M2.6 5.1l1.6 1.6 3.2-3.3" stroke="#fff" stroke-width="1.3" fill="none"/></svg>Phasellus pellentesque</li>
    </ul>
  </div>
  <div class="abs col" style="left:583px;height:150px">
    <h4 class="accent">Recent Blog Post</h4>
    <div class="post" style="top:27px">
      <div class="title">Mauris vel lacus vitae felis</div>
      <p>volutpat Etiam est nunc venenatis in tristique eu imperdiet ac<br>nisl Cum sociis natoque penatibus et magnis dis</p>
      <span class="date">25 May 2015</span>
    </div>
    <div class="post" style="top:96px">
      <div class="title">Donec dictum lectus non odio</div>
      <p>volutpat Etiam est nunc venenatis in tristique eu imperdiet ac<br>nisl Cum sociis natoque penatibus et magnis dis</p>
      <span class="date">25 May 2015</span>
    </div>
  </div>
  <a class="abs btn btn-light" href="#">Physician Toolbox</a>
  <a class="abs btn btn-dark" href="#">Book an Appointment</a>
</section>

<footer class="abs footer">
  <h5 style="left:148px">COMPANY</h5>
  <div class="links">
    <a style="left:148px;top:55px">About Us</a>
    <a style="left:148px;top:75px">Careers</a>
    <a style="left:148px;top:95px">Events</a>
    <a style="left:148px;top:115px">Investor Relations</a>
    <a style="left:266px;top:55px">Support</a>
    <a style="left:266px;top:75px">Partners</a>
    <a style="left:266px;top:95px">Term of Use</a>
    <a style="left:266px;top:115px">Contact Us</a>
  </div>
  <h5 style="left:368px">RECENT TWEETS</h5>
  <p class="tweet" style="top:54px">Plan your trip for #MCX15. Check out hotel &amp; travel recommendations and experience all that Boston has to offer! http://lnk.example/4QzTr</p>
  <p class="tweet" style="top:101px">Plan your trip for #MCX15. Check out hotel &amp; travel recommendations and experience all that Boston has to offer! http://lnk.example/4QzTr</p>
  <h5 style="left:628px">FOLLOW US</h5>
  <p class="follow">Connect with us any where on these</p>
</footer>
<div class="abs bottom">© 2015 Company Name &nbsp;All right reserved &nbsp;Term of Use</div>

</body>
</html>
```